Coffeeshop menu for filter tip

We want to have a cannabis (coffeeshop) menu in the size 25mm wide x 60mm wide. Some examples attached.

it must have the following text:
Menu

WEED p/g
Oblivane €16
Cloudplum €14
Tide Runner €14
Quincefig €16
Mega Marsh €14
Grey Heron €14

HASH p/g
Tashar Amber €12
Pebble Frost€11
Lime Dunes €14
Ash Petal €10

Target Market(s)

tourist in Amsterdam

Requirements
Nice to have
• cannabis sign leaf
• No Cigarettes allowed symbol

```html
<!DOCTYPE html>
<html lang="en">
<head>
<meta charset="utf-8">
<title>Coffeeshop Menu</title>
<link href="https://fonts.googleapis.com/css2?family=Josefin+Sans:wght@400&family=Montserrat:wght@200;300;400&family=Raleway:wght@400&family=Open+Sans:wght@700&display=swap" rel="stylesheet">
<style>
  :root {
    --bg-top: #121212;
    --bg-mid: #1f1f1f;
    --bg-low: #2a2a2a;
    --panel: #000000;
    --gold: #f2e21a;
    --white: #ffffff;
    --muted: #9a9a9a;
    --menu-grey: #cfcfcf;
    --badge-red: #8b1a1a;
    --sign-red: #c0262c;
    --skyline: #0b0b0b;
  }
  * { margin: 0; padding: 0; box-sizing: border-box; }
  html, body { width: 1200px; height: 2880px; overflow: hidden; }
  body {
    position: relative;
    background: linear-gradient(180deg, var(--bg-top) 0%, var(--bg-mid) 50%, var(--bg-low) 82%, var(--bg-mid) 92%);
    font-family: "Josefin Sans", sans-serif;
  }
  .leaf-decoration {
    position: absolute; inset: 0 0 224px 0;
    background:
      radial-gradient(ellipse 700px 900px at 1050px 200px, rgba(255,255,255,0.05), transparent 70%),
      radial-gradient(ellipse 600px 800px at 150px 1300px, rgba(255,255,255,0.04), transparent 70%),
      radial-gradient(ellipse 700px 700px at 1000px 1800px, rgba(0,0,0,0.35), transparent 70%),
      radial-gradient(ellipse 800px 500px at 300px 2300px, rgba(255,255,255,0.035), transparent 70%);
  }
  .no-cig-badge {
    position: absolute; left: 66px; top: 66px; width: 209px; height: 158px;
    border: 3px solid var(--badge-red); border-radius: 8px;
    background: #000;
  }
  .no-cig-badge svg { position: absolute; left: 14px; top: 12px; }
  .no-cig-badge .badge-label {
    position: absolute; left: 0; right: 0; bottom: 12px; text-align: center;
    font-family: "Open Sans", sans-serif; font-weight: 700; font-size: 27px;
    color: var(--white); letter-spacing: 0.02em;
  }
  .section-title {
    position: absolute; font-family: "Montserrat", sans-serif; font-weight: 400;
    color: var(--white); font-size: 112px; line-height: 1; letter-spacing: 0.5em;
  }
  .weed-title { left: 422px; top: 262px; }
  .hash-title { left: 147px; top: 1553px; }
  .price-tab {
    position: absolute; background: var(--panel);
    font-family: "Raleway", sans-serif; font-size: 48px; color: var(--muted);
    text-align: center;
  }
  .weed-tab { left: 981px; top: 298px; width: 129px; height: 92px; padding-top: 38px; }
  .hash-tab { left: 728px; top: 1589px; width: 182px; height: 92px; padding-top: 38px; }
  .price-panel { position: absolute; background: var(--panel); }
  .weed-panel { left: 349px; top: 389px; width: 761px; height: 827px; padding: 46px 48px 0 51px; }
  .hash-panel { left: 80px; top: 1680px; width: 830px; height: 568px; padding: 38px 72px 0 53px; }
  .menu-row {
    display: grid; grid-template-columns: 1fr 110px; align-items: center;
    height: 125px;
  }
  .item-name {
    color: var(--gold); font-weight: 400; font-size: 48px; line-height: 1;
    letter-spacing: 0.3em; text-transform: uppercase; white-space: nowrap;
  }
  .item-price {
    color: var(--white); font-family: "Montserrat", sans-serif; font-weight: 300;
    font-size: 58px; line-height: 1; text-align: right; white-space: nowrap;
    letter-spacing: -0.02em;
  }
  .skyline {
    position: absolute; left: 0; right: 0; top: 2448px; height: 208px;
    background: linear-gradient(180deg, transparent 0%, rgba(11,11,11,0.6) 55%, var(--skyline) 100%);
  }
  .menu-band {
    position: absolute; left: 0; right: 0; bottom: 0; height: 224px; background: var(--panel);
  }
  .menu-word {
    position: absolute; left: 285px; top: 2688px;
    font-family: "Montserrat", sans-serif; font-weight: 200; font-size: 158px; line-height: 1;
    letter-spacing: 0.42em; color: var(--menu-grey);
  }
</style>
</head>
<body>
  <div class="leaf-decoration" role="img" aria-label="Faint cannabis leaf outlines scattered across the dark background"></div>

  <div class="no-cig-badge">
    <svg width="180" height="90" viewBox="0 0 180 90" aria-hidden="true">
      <text x="0" y="80" font-family="Open Sans, sans-serif" font-weight="700" font-size="104" fill="#ffffff">N</text>
      <circle cx="127" cy="45" r="36" fill="none" stroke="var(--sign-red)" stroke-width="9"/>
      <rect x="100" y="40" width="52" height="10" fill="#ffffff"/>
      <rect x="140" y="40" width="12" height="10" fill="#777"/>
      <line x1="101" y1="19" x2="153" y2="71" stroke="var(--sign-red)" stroke-width="9"/>
    </svg>
    <div class="badge-label">CIGARETTES</div>
  </div>

  <h1 class="section-title weed-title">WEED</h1>
  <div class="price-tab weed-tab">p/g</div>
  <div class="price-panel weed-panel">
    <div class="menu-row"><span class="item-name">Oblivane</span><span class="item-price">€16</span></div>
    <div class="menu-row"><span class="item-name">Cloudplum</span><span class="item-price">€14</span></div>
    <div class="menu-row"><span class="item-name">Tide Runner</span><span class="item-price">€14</span></div>
    <div class="menu-row"><span class="item-name">Quincefig</span><span class="item-price">€16</span></div>
    <div class="menu-row"><span class="item-name">Mega Marsh</span><span class="item-price">€14</span></div>
    <div class="menu-row"><span class="item-name">Grey Heron</span><span class="item-price">€14</span></div>
  </div>

  <h2 class="section-title hash-title">HASH</h2>
  <div class="price-tab hash-tab">p/g</div>
  <div class="price-panel hash-panel">
    <div class="menu-row"><span class="item-name">Tashar Amber</span><span class="item-price">€12</span></div>
    <div class="menu-row"><span class="item-name">Pebble Frost</span><span class="item-price">€11</span></div>
    <div class="menu-row"><span class="item-name">Lime Dunes</span><span class="item-price">€14</span></div>
    <div class="menu-row"><span class="item-name">Ash Petal</span><span class="item-price">€10</span></div>
  </div>

  <div class="skyline" role="img" aria-label="Amsterdam city skyline silhouette with towers and canal houses"></div>
  <div class="menu-band"></div>
  <div class="menu-word">MENU</div>
</body>
</html>
```